Quillon Glazing

Modern glazing company specializing in commercial fit outs, pool fencing, frameless showers and glass splash backs, im after a very young/modern logo, it doesnt have to be revelent to glazing and a classy "boss like" design for the card. thank you in advanced

im thinking carbon fiber back ground or something along that line with bright orange wording or something maybe, open to suggestions 

Industry/Entity Type

Fencing

Contact Information for Business Card

company name, name, phone and products

```html
<!DOCTYPE html>
<html lang="en">
<head>
<meta charset="utf-8">
<title>Quillon Glazing – Business Card</title>
<link rel="stylesheet" href="https://fonts.googleapis.com/css2?family=Open+Sans:wght@700;800&display=swap">
<style>
  :root {
    --canvas-bg: #e9e6e2;
    --charcoal: #2d2c2e;
    --orange: #f15a24;
    --orange-faint: #f36a38;
    --white: #ffffff;
    --card-w: 600px;
    --card-h: 343px;
  }
  * { box-sizing: border-box; margin: 0; padding: 0; }
  html, body {
    width: 1200px;
    height: 1000px;
    overflow: hidden;
    background: var(--canvas-bg);
    font-family: "Open Sans", Arial, sans-serif;
  }
  .canvas {
    position: relative;
    width: 1200px;
    height: 1000px;
  }
  .card {
    position: absolute;
    width: var(--card-w);
    height: var(--card-h);
    overflow: hidden;
    border-radius: 4px;
    box-shadow: 0 6px 18px rgba(0,0,0,0.18);
  }
  .side-tab {
    position: absolute;
    top: 50%;
    width: 60px;
    height: 250px;
    transform: translateY(-50%);
    border-radius: 30px;
  }
  .side-tab--left { left: -32px; }
  .side-tab--right { right: -32px; }

  /* Front card */
  .card--front {
    left: 110px;
    top: 90px;
    background: var(--charcoal);
  }
  .card--front .side-tab { background: var(--orange); }
  .front-brand {
    position: absolute;
    inset: 0;
    display: flex;
    align-items: center;
    justify-content: center;
  }
  .front-brand__name {
    color: var(--orange);
    font-weight: 800;
    font-size: 44px;
    letter-spacing: 1px;
  }

  /* Back card */
  .card--back {
    left: 490px;
    top: 520px;
    background: var(--orange);
  }
  .card--back .side-tab { background: var(--charcoal); }
  .back-watermark {
    position: absolute;
    left: 0;
    right: 0;
    top: 254px;
    text-align: center;
    color: var(--orange-faint);
    font-weight: 800;
    font-size: 34px;
    line-height: 1;
    letter-spacing: 1px;
  }
  .back-content {
    position: absolute;
    left: 0;
    right: 0;
    top: 34px;
    text-align: center;
    color: var(--white);
    font-weight: 700;
  }
  .back-brand {
    font-size: 26px;
    font-weight: 800;
    letter-spacing: 0.5px;
  }
  .back-person {
    margin-top: 30px;
    font-size: 24px;
    font-weight: 800;
  }
  .back-services {
    margin-top: 6px;
    font-size: 15px;
    line-height: 1.35;
  }
  .back-phone {
    position: absolute;
    right: 46px;
    top: 218px;
    color: var(--white);
    font-size: 16px;
    line-height: 1.3;
    font-weight: 700;
  }
  .back-email {
    position: absolute;
    left: 20px;
    bottom: 12px;
    color: var(--white);
    font-size: 16px;
    font-weight: 700;
  }
</style>
</head>
<body>
<main class="canvas">
  <section class="card card--front" aria-label="Business card front">
    <span class="side-tab side-tab--left"></span>
    <span class="side-tab side-tab--right"></span>
    <div class="front-brand">
      <span class="front-brand__name">QUILLON GLAZING</span>
    </div>
  </section>

  <section class="card card--back" aria-label="Business card back">
    <span class="side-tab side-tab--left"></span>
    <span class="side-tab side-tab--right"></span>
    <div class="back-watermark" aria-hidden="true">QUILLON GLAZING</div>
    <div class="back-content">
      <p class="back-brand">QUILLON GLAZING</p>
      <p class="back-person">DANE WHITLOCK</p>
      <p class="back-services">Commercial fit outs , Pool fencing ,<br>Frameless showers , Glass splash backs.</p>
    </div>
    <p class="back-phone">Phone : 0400 555 172</p>
    <p class="back-email">Email : Your email id over here.</p>
  </section>
</main>
</body>
</html>
```